Business Card Design

We are a manufacturing and distribution company with most of our customer base being supermarkets. We have established brand guidelines that are attached.

```html
<!DOCTYPE html>
<html lang="en">
<head>
<meta charset="utf-8">
<title>Korvane Business Card</title>
<link href="https://fonts.googleapis.com/css2?family=Montserrat:wght@500;700&family=Open+Sans:wght@400&display=swap" rel="stylesheet">
<style>
  :root {
    --stage: #2a2a2c;
    --card-black: #0b0b0c;
    --card-white: #ffffff;
    --ink: #111111;
    --brand-red: #e3232f;
    --brand-blue: #1e6db4;
    --rule: #444444;
    --text: #1a1a1a;
  }
  html, body {
    margin: 0;
    padding: 0;
    width: 1200px;
    height: 1108px;
    overflow: hidden;
    background: var(--stage);
  }
  .canvas {
    position: relative;
    width: 1200px;
    height: 1108px;
  }
  .card {
    position: absolute;
    top: 184px;
    width: 420px;
    height: 740px;
    border-radius: 28px;
    overflow: hidden;
    box-shadow: 0 18px 40px rgba(0,0,0,0.45);
  }
  /* Back side */
  .card--back {
    left: 150px;
    background: var(--card-black);
  }
  .back-pattern {
    position: absolute;
    inset: 0;
    background: linear-gradient(160deg, #0a0a0b 0%, #151516 45%, #2b2b2d 100%);
  }
  .back-wordmark {
    position: absolute;
    left: 0;
    right: 0;
    bottom: 92px;
    text-align: center;
    font-family: "Montserrat", sans-serif;
    font-weight: 700;
    font-size: 40px;
    letter-spacing: 2px;
    color: #ffffff;
  }
  /* Front side */
  .card--front {
    left: 630px;
    background: var(--card-white);
    text-align: center;
    color: var(--text);
  }
  .brand {
    margin-top: 196px;
    display: flex;
    flex-direction: column;
    align-items: center;
  }
  .brand-square {
    width: 46px;
    height: 46px;
    background: var(--brand-red);
    margin-bottom: 14px;
  }
  .brand-name {
    font-family: "Montserrat", sans-serif;
    font-weight: 700;
    font-size: 58px;
    letter-spacing: 1px;
    color: var(--ink);
    line-height: 1;
  }
  .person-name {
    margin-top: 22px;
    font-family: "Montserrat", sans-serif;
    font-weight: 700;
    font-size: 34px;
    color: var(--brand-red);
    line-height: 1;
  }
  .person-role {
    margin-top: 6px;
    font-family: "Open Sans", sans-serif;
    font-size: 19px;
  }
  .icon-row {
    margin: 8px auto 0;
    width: 340px;
    display: flex;
    align-items: center;
    gap: 6px;
  }
  .icon-row .rule {
    flex: 1;
    height: 1px;
    background: var(--rule);
  }
  .icon {
    width: 32px;
    height: 32px;
    border-radius: 5px;
    background: var(--brand-blue);
    display: flex;
    align-items: center;
    justify-content: center;
  }
  .contact {
    margin-top: 12px;
    font-family: "Open Sans", sans-serif;
    font-size: 20px;
    line-height: 1.4;
  }
  .address {
    margin: 14px auto 0;
    width: 340px;
    padding: 8px 0 10px;
    border-top: 1px solid var(--rule);
    border-bottom: 1px solid var(--rule);
    font-family: "Open Sans", sans-serif;
    font-size: 19px;
    line-height: 1.3;
  }
</style>
</head>
<body>
<div class="canvas">
  <section class="card card--back">
    <div class="back-pattern" role="img" aria-label="Repeating brand monogram pattern in glossy black tones"></div>
    <div class="back-wordmark">KORVANE</div>
  </section>

  <section class="card card--front">
    <div class="brand">
      <div class="brand-square"></div>
      <div class="brand-name">KORVANE</div>
    </div>
    <div class="person-name">MARA QUELL</div>
    <div class="person-role">Manager</div>
    <div class="icon-row">
      <span class="rule"></span>
      <span class="icon">
        <svg width="20" height="20" viewBox="0 0 24 24" fill="none" stroke="#fff" stroke-width="2" stroke-linecap="round" stroke-linejoin="round"><path d="M5 3h4l2 5-2.5 1.5a11 11 0 0 0 6 6L16 13l5 2v4a2 2 0 0 1-2 2A17 17 0 0 1 3 5a2 2 0 0 1 2-2z"/></svg>
      </span>
      <span class="icon">
        <svg width="20" height="20" viewBox="0 0 24 24" fill="none" stroke="#fff" stroke-width="2" stroke-linejoin="round"><rect x="3" y="5" width="18" height="14" rx="1"/><path d="M3 6l9 7 9-7"/></svg>
      </span>
      <span class="icon">
        <svg width="20" height="20" viewBox="0 0 24 24" fill="none" stroke="#fff" stroke-width="1.8"><circle cx="12" cy="12" r="9"/><ellipse cx="12" cy="12" rx="4" ry="9"/><path d="M3 12h18M5 7h14M5 17h14"/></svg>
      </span>
      <span class="rule"></span>
    </div>
    <div class="contact">
      <div>(555) 014-2780</div>
      <div>info@korvanemail.com</div>
      <div>www.korvane.com</div>
    </div>
    <div class="address">
      <div>4820 Orchard Row, Suite 210</div>
      <div>Fairhaven, TX 0000</div>
    </div>
  </section>
</div>
</body>
</html>
```